Corporate Business Card

Very professional, Modern, Not to busy, include phone address email, website
(253) 617-4930, 18761 52nd Avenue S, Kent, WA 98047, martin@plumlinegroup.com, varkoworks.com

Target Market(s)

Manufacturing

Industry/Entity Type

Aero, machining, manufacturing, Off road racing

Contact Information for Business Card

Phone, address email, website

```html
<!DOCTYPE html>
<html lang="en">
<head>
<meta charset="utf-8">
<title>Varko Works — Business Card</title>
<link rel="stylesheet" href="https://fonts.googleapis.com/css2?family=Exo+2:wght@600;700&family=Roboto:wght@400&display=swap">
<style>
  :root {
    --backdrop: #2a2a2a;
    --front-top: #141415;
    --front-bottom: #2a2a2c;
    --logo-grey: #6a6a6c;
    --navy: #283766;
    --navy-deep: #25335f;
    --red: #c9202f;
    --white: #f2f3f6;
    --soft-white: #dfe3ee;
  }
  * { margin: 0; padding: 0; box-sizing: border-box; }
  html, body { width: 1200px; height: 1138px; overflow: hidden; }
  body { background: var(--backdrop); position: relative; font-family: "Roboto", sans-serif; }

  .card { position: absolute; width: 620px; height: 375px; border-radius: 16px; overflow: hidden; }

  .card-front {
    left: 274px; top: 186px;
    background: linear-gradient(160deg, var(--front-top) 0%, #1d1d1f 55%, var(--front-bottom) 100%);
  }
  .front-wordmark {
    position: absolute; left: 0; right: 0; top: 118px;
    text-align: center;
    font-family: "Exo 2", sans-serif; font-weight: 700;
    font-size: 60px; letter-spacing: 2px; line-height: 1;
    color: var(--logo-grey);
  }
  .front-website {
    position: absolute; left: 0; right: 0; top: 328px;
    text-align: center;
    font-size: 16px; letter-spacing: 10px;
    color: var(--white);
  }
  .front-website .accent { color: var(--red); }

  .card-back {
    left: 276px; top: 608px;
    background: linear-gradient(180deg, var(--navy) 0%, var(--navy-deep) 100%);
    color: var(--white);
  }
  .holder-name {
    position: absolute; left: 35px; top: 85px;
    font-family: "Exo 2", sans-serif; font-weight: 700;
    font-size: 26px; letter-spacing: 0.5px; line-height: 1;
  }
  .holder-name .surname { color: var(--red); }
  .name-rule {
    position: absolute; left: 34px; top: 129px;
    width: 424px; height: 2px; background: var(--white);
  }
  .back-wordmark {
    position: absolute; right: 36px; top: 78px;
    font-family: "Exo 2", sans-serif; font-weight: 700;
    font-size: 38px; letter-spacing: 1px; line-height: 1;
    color: var(--white);
  }

  .contact-list { position: absolute; left: 36px; top: 270px; list-style: none; }
  .contact-list li {
    display: flex; align-items: center; gap: 13px;
    height: 24px; font-size: 17px; color: var(--soft-white);
  }
  .contact-list svg { width: 14px; height: 14px; flex: none; }

  .address {
    position: absolute; right: 64px; top: 293px;
    text-align: right; font-size: 17px; line-height: 25px; color: var(--soft-white);
  }
  .address-pin { position: absolute; right: 36px; top: 295px; width: 16px; height: 20px; }
</style>
</head>
<body>

<section class="card card-front" aria-label="Card front">
  <div class="front-wordmark">VARKO WORKS</div>
  <div class="front-website">www.varko<span class="accent">works</span>.com</div>
</section>

<section class="card card-back" aria-label="Card back">
  <div class="holder-name">MARTIN <span class="surname">HALE</span></div>
  <div class="name-rule"></div>
  <div class="back-wordmark">VARKO WORKS</div>

  <ul class="contact-list">
    <li>
      <svg viewBox="0 0 16 16" aria-hidden="true"><path fill="#c9202f" d="M1 5c0-2 3-3 7-3s7 1 7 3v1h-4V5H5v1H1zM4 7h8l2 6H2z"/><circle cx="8" cy="10" r="1.8" fill="#283766"/></svg>
      (253) 617-4930
    </li>
    <li>
      <svg viewBox="0 0 16 16" aria-hidden="true"><rect x="1" y="3" width="14" height="10" rx="1" fill="#c9202f"/><path d="M1.5 3.5 8 9l6.5-5.5" fill="none" stroke="#283766" stroke-width="1.3"/></svg>
      martin@plumlinegroup.com
    </li>
    <li>
      <svg viewBox="0 0 16 16" aria-hidden="true"><g fill="none" stroke="#c9202f" stroke-width="1.4"><circle cx="8" cy="8" r="6.3"/><ellipse cx="8" cy="8" rx="2.8" ry="6.3"/><path d="M1.8 8h12.4M3 4.6h10M3 11.4h10"/></g></svg>
      www.varkoworks.com
    </li>
  </ul>

  <div class="address">18761 52nd Avenue S,<br>Kent, WA 98047</div>
  <svg class="address-pin" viewBox="0 0 16 20" aria-hidden="true"><path fill="#c9202f" d="M8 0a7 7 0 0 0-7 7c0 5 7 13 7 13s7-8 7-13a7 7 0 0 0-7-7z"/><circle cx="8" cy="7" r="2.6" fill="#283766"/></svg>
</section>

</body>
</html>
```